Animation College website

Name of College: Brightloom Academy of 3D Animation and VFX

We need a redesigned modern website for Brightloom. The web-design should communicate a VFX and animation school and education. We will also need full access to the website once completed. We will also need access to the website to be able to make changes to the content and site ideally the website would be built on Wordpress.

To learn more about what the College please visit: http://brightloom-academy.example/
The video on the homepage demonstrates why Brightloom is a unique college offering 3D animation and VFX. The direct link to the video can be watched here: https://videohost.example/482915036

Client Profile Summary: Brightloom is an improved concept in job skills training for the 3D animation and visual effects industries. Our high graduate job placement numbers are based on the assertion that job skills must include more than simply learning to use software tools. Where nearly every digital media program teaches tools, job skills training should be about learning how to do a job in addition to learning how to use software tools. Brightloom is taught in an apprenticeship style with very experienced faculty mentoring and teaching students to learn how to master their craft (VFX and animation) so they can seamlessly step into industry and excel.

Target Market(s)

High school students, students interested in learning about animation and 3D.

Industry/Entity Type

College

Coding

Coded - Design and coding required

Number of Pages Required

5+ page

Font styles to use
Sans Serif

Colors

Designer to choose colors to be used in the design.

Requirements
Must have
• Please include the video on the current Brightloom-academy.example website. https://videohost.example/482915036
• Use the same content on the current brightloom-academy.example website.
• Include a page to showcase student work.
• Website must also be mobile responsive.
Should not have
• The attached PDF of the landing page is just an example of something we like. You do not have to replicate this. The PDF landing page is showing the colour blue you should incorporate.

```html
<!DOCTYPE html>
<html lang="en">
<head>
<meta charset="utf-8">
<title>Brightloom Academy of 3D Animation and VFX</title>
<link rel="stylesheet" href="https://fonts.googleapis.com/css2?family=Jost:ital,wght@0,400;0,500;1,500&family=Open+Sans:ital,wght@0,400;0,600;1,600;1,700&display=swap">
<style>
:root{
  --blue:#1a6fc4;
  --blue-deep:#1560b0;
  --blue-band:#1f74cc;
  --navy:#1d2733;
  --ink:#222b33;
  --body:#6a6f75;
  --gray-band:#6e6f71;
  --white:#ffffff;
  --field:#2c3440;
}
*{box-sizing:border-box;margin:0;padding:0}
html,body{width:1200px;height:3622px;overflow:hidden;background:var(--white)}
body{position:relative;font-family:"Open Sans",Arial,sans-serif;color:var(--body)}
.section{position:absolute;left:0;width:1200px}
.abs{position:absolute}
.heading{font-family:"Jost",Arial,sans-serif;font-weight:400;color:var(--ink);text-transform:uppercase;letter-spacing:.5px}
.rule{position:absolute;height:3px;width:70px;background:var(--blue)}
.lead{font-family:"Jost",Arial,sans-serif;font-weight:500;color:var(--blue);font-size:18px}
.copy{font-size:12.5px;line-height:19px;color:var(--body)}

/* header */
.site-header{top:0;height:101px;background:var(--white);border-bottom:4px solid var(--blue)}
.brand{left:133px;top:20px;display:flex;align-items:center;gap:12px}
.brand-dot{width:60px;height:60px;border-radius:50%;background:var(--blue)}
.brand-name{font-family:"Jost",Arial,sans-serif;font-weight:500;font-size:32px;color:var(--blue);line-height:34px;letter-spacing:.5px}
.brand-tag{font-family:"Jost",Arial,sans-serif;font-weight:500;font-size:12px;color:var(--blue);line-height:14px}
.main-nav{left:483px;top:40px;display:flex;gap:30px;font-family:"Jost",Arial,sans-serif;font-size:12.5px;color:var(--ink);text-transform:uppercase}

/* hero */
.hero{top:101px;height:522px}
.hero-photo{position:absolute;inset:0;background:linear-gradient(120deg,#2e3640 0%,#4d5966 38%,#8a96a3 60%,#3b4550 100%)}
.hero-arrow{position:absolute;top:240px;width:30px;height:56px;background:rgba(0,0,0,.45)}
.hero-title{left:140px;top:353px;width:524px;height:82px;background:rgba(10,14,20,.72);color:var(--white);font-family:"Jost",Arial,sans-serif;font-weight:500;font-size:21px;line-height:26px;padding:14px 18px;text-transform:uppercase}
.hero-sub{left:140px;top:435px;width:524px;height:44px;background:rgba(20,26,34,.88);color:var(--white);font-family:"Jost",Arial,sans-serif;font-size:18px;padding:10px 18px}
.enquiry{left:789px;top:0;width:375px;height:490px;background:rgba(22,28,36,.82)}
.enquiry-head{height:44px;background:var(--blue);color:var(--white);font-family:"Jost",Arial,sans-serif;font-size:19px;text-align:center;line-height:44px;letter-spacing:.5px}
.enquiry-intro{position:absolute;top:66px;left:0;width:375px;text-align:center;color:var(--white);font-size:12px;font-weight:600;line-height:17px}
.field{position:absolute;left:22px;width:234px;border:1px solid #c7ccd2;background:var(--field);color:#dfe3e8;font-size:11px;padding:6px 8px}
.send-btn{position:absolute;left:22px;top:449px;width:234px;height:32px;background:var(--blue);color:var(--white);font-family:"Jost",Arial,sans-serif;font-size:13px;text-align:center;line-height:32px;letter-spacing:.5px}

/* partner band */
.partners{top:623px;height:145px;background:var(--blue-band)}
.badge{position:absolute;top:24px;width:96px;height:96px;border-radius:50%;border:3px solid var(--white);background:rgba(255,255,255,.12)}

/* photo circles */
.photo-ring{position:absolute;width:272px;height:272px;border-radius:50%;border:2px dotted #b9bec4;padding:8px}
.photo-ring .photo{width:100%;height:100%;border-radius:50%}

/* videos */
.videos{top:1166px;height:809px;background:var(--gray-band)}
.videos-photo{position:absolute;left:0;top:0;width:1200px;height:471px;background:linear-gradient(160deg,#1f252c,#39434e 50%,#262d35)}
.video-frame{left:237px;top:203px;width:724px;height:338px;border:5px solid var(--white);background:linear-gradient(120deg,#2a2622,#6b5140 45%,#3a3a3e)}
.btn-outline{left:507px;top:695px;width:186px;height:39px;background:var(--blue);border:2px solid var(--white);color:var(--white);font-size:12px;text-align:center;line-height:35px;text-transform:uppercase;font-family:"Jost",Arial,sans-serif}

/* list */
.ticks{list-style:none}
.ticks li{position:relative;padding-left:24px;font-size:12.5px;line-height:19px;margin-bottom:19px}
.ticks li svg{position:absolute;left:0;top:3px}

/* testimonials */
.testimonials{top:2503px;height:474px;background:linear-gradient(180deg,#1b65b4,#2a7fd4 50%,#1b65b4)}
.quote{left:193px;top:213px;width:821px;text-align:center;color:var(--white);font-weight:700;font-style:italic;font-size:15px;line-height:21px}

/* advantage list */
.numbered{list-style:none}
.numbered li{display:flex;align-items:center;gap:10px;font-size:11.5px;height:29px;color:var(--body);white-space:nowrap}
.num{width:18px;height:18px;border-radius:50%;background:var(--blue);color:var(--white);font-size:10px;font-weight:600;display:flex;align-items:center;justify-content:center;flex:none}

.cta{top:3423px;height:121px;background:var(--blue-deep);text-align:center;color:var(--white);font-family:"Jost",Arial,sans-serif}
.site-footer{top:3544px;height:78px;background:var(--white)}
.footer-brand{left:133px;top:22px;display:flex;align-items:center;gap:7px}
.footer-dot{width:30px;height:30px;border-radius:50%;background:var(--blue)}
.footer-name{font-family:"Jost",Arial,sans-serif;font-weight:500;font-size:15px;color:var(--blue)}
.copyright{left:290px;top:22px;font-size:11px;line-height:16px;color:var(--body)}
.social{width:22px;height:22px;border-radius:50%;border:2px solid var(--blue);display:inline-block}
</style>
</head>
<body>

<header class="section site-header">
  <div class="abs brand">
    <div class="brand-dot"></div>
    <div>
      <div class="brand-name">BRIGHTLOOM</div>
      <div class="brand-tag">School of 3D Animation &amp; VFX</div>
    </div>
  </div>
  <nav class="abs main-nav">
    <span>How to pick a school</span><span>Admission</span><span>Training</span><span>Philosophy</span><span>Faculty &amp; Staff</span><span>Apply</span><span>Blog</span>
  </nav>
</header>

<section class="section hero">
  <div class="hero-photo" role="img" aria-label="Students working at animation workstations in a dark studio"></div>
  <div class="hero-arrow" style="left:0"><svg width="30" height="56"><path d="M18 20l-8 8 8 8" stroke="#fff" stroke-width="3" fill="none"/></svg></div>
  <div class="hero-arrow" style="right:0"><svg width="30" height="56"><path d="M12 20l8 8-8 8" stroke="#fff" stroke-width="3" fill="none"/></svg></div>
  <div class="abs hero-title">3D Animation &amp; VFX One - Year Intensive Training Program</div>
  <div class="abs hero-sub">Train Alongside Passionate Experienced Industry Masters</div>

  <form class="abs enquiry">
    <div class="enquiry-head">WANT TO KNOW MORE</div>
    <p class="enquiry-intro">Complete This Form to Receive more<br>Information about Program Details &amp; More!</p>
    <div class="field" style="top:140px;height:30px">First Name*</div>
    <div class="field" style="top:184px;height:30px">Last Name*</div>
    <div class="field" style="top:225px;height:30px">Phone*</div>
    <div class="field" style="top:266px;height:30px">Email*</div>
    <div class="field" style="top:307px;height:31px">Country Of Residence*</div>
    <div class="field" style="top:350px;height:90px">Comments*</div>
    <div class="send-btn">SEND ME FREE INFO</div>
  </form>
</section>

<section class="section partners">
  <div class="badge" style="left:198px"></div>
  <div class="badge" style="left:432px"></div>
  <div class="badge" style="left:669px"></div>
  <div class="badge" style="left:906px"></div>
</section>

<section class="section" style="top:768px;height:398px">
  <h2 class="abs heading" style="left:133px;top:50px;font-size:26px;line-height:32px">One-Year Intensive Training<br>Program</h2>
  <div class="rule" style="left:133px;top:134px"></div>
  <p class="abs lead" style="left:133px;top:148px">An exciting, comprehensive program with a 100% graduate employment rate</p>
  <p class="abs copy" style="left:133px;top:188px;width:600px">The 48-week Brightloom One-Year Intensive Training Program is designed to provide students the practical skills and real-world experience needed to thrive in the film and TV animation, and VFX industries. Students are mentored by our passionate instructors who have extensive industry experience. Each of our instructors knows exactly what it takes for students to be successful. We carefully crafted the program curriculum to teach students how to function in a real production team so that they can be highly effective professionals once they enter the workforce.</p>
  <div class="photo-ring" style="left:789px;top:62px"><div class="photo" role="img" aria-label="Student presenting work in a dark screening room" style="background:radial-gradient(circle at 40% 40%,#d8cfc4,#6a4a3a 45%,#1c1a1c 80%)"></div></div>
</section>

<section class="section videos">
  <div class="videos-photo" role="img" aria-label="Dim studio with students at computer screens"></div>
  <h2 class="abs heading" style="left:0;top:52px;width:1200px;text-align:center;color:#fff;font-size:28px">Videos</h2>
  <div class="abs" style="left:570px;top:92px;width:60px;height:2px;background:#fff"></div>
  <p class="abs" style="left:160px;top:104px;width:880px;text-align:center;color:#fff;font-size:12px;line-height:18px">Brightloom is an improved concept in job skills training for the 3D animation and visual effects industries. Our high graduate job placement numbers are based on the assertion that job skills must include more than simply learning to use software tools. Where nearly</p>
  <div class="abs video-frame" role="img" aria-label="Video still of an instructor speaking in the studio">
    <svg class="abs" style="left:309px;top:116px" width="96" height="96" viewBox="0 0 96 96"><circle cx="48" cy="48" r="44" fill="rgba(0,0,0,.25)" stroke="#fff" stroke-width="5"/><path d="M38 30l30 18-30 18z" fill="#fff"/></svg>
  </div>
  <p class="abs" style="left:190px;top:592px;width:820px;text-align:center;color:#fff;font-size:12px;line-height:22px">every digital media program teaches tools, job skills training should be about learning how to do a job in addition to learning how to use software tools. Brightloom is taught in an apprenticeship style with very experienced faculty mentoring and teaching students to learn how to master their craft (VFX and animation) so they can seamlessly step into industry and excel.</p>
  <div class="abs btn-outline">View more information</div>
</section>

<section class="section" style="top:1975px;height:528px">
  <div class="photo-ring" style="left:130px;top:74px"><div class="photo" role="img" aria-label="Student smiling at a workstation" style="background:radial-gradient(circle at 45% 45%,#c9a48a,#4d3a34 50%,#15181c 85%)"></div></div>
  <h2 class="abs heading" style="left:502px;top:62px;font-size:26px;line-height:34px">Learn Animation &amp; Visual Effects<br>Production from the Experts</h2>
  <div class="rule" style="left:502px;top:147px"></div>
  <p class="abs lead" style="left:502px;top:175px">The world's first and sole simulated production training program</p>
  <p class="abs copy" style="left:502px;top:210px;width:580px">Our philosophy is unique. We don't focus on grades. Instead, we focus on preparing each of our students for the challenges of working as 3D artists such as animators, lighting TDs, riggers, modellers, compositors and more. Our instructors teach you until you're confident in your skills. If you need more help, we train you until you're ready.</p>
  <p class="abs" style="left:502px;top:322px;width:600px;color:var(--blue);font-size:12px;font-weight:600">Students grasp valuable skills that employers are looking for over the course of three intensive terms:</p>
  <ul class="abs ticks" style="left:512px;top:354px;width:570px">
    <li><svg width="14" height="12"><path d="M1 6l4 4 8-9" stroke="#1a6fc4" stroke-width="2.4" fill="none"/></svg>Core Skills: An intensive introduction to skills involving cameras, modeling, animation, dynamics, lighting, composition, production, and more</li>
    <li><svg width="14" height="12"><path d="M1 6l4 4 8-9" stroke="#1a6fc4" stroke-width="2.4" fill="none"/></svg>Transition into Practice: Expand on core skills with advanced training and team production</li>
    <li><svg width="14" height="12"><path d="M1 6l4 4 8-9" stroke="#1a6fc4" stroke-width="2.4" fill="none"/></svg>Practical Training: Practical hands-on production and dailies training</li>
  </ul>
</section>

<section class="section testimonials" role="img" aria-label="Blue-tinted studio backdrop behind testimonial">
  <h2 class="abs heading" style="left:0;top:56px;width:1200px;text-align:center;color:#fff;font-size:26px">Industry Testimonials</h2>
  <div class="abs" style="left:570px;top:100px;width:60px;height:2px;background:#fff"></div>
  <div class="abs" style="left:200px;top:168px;width:360px;border-top:2px dotted rgba(255,255,255,.8)"></div>
  <div class="abs" style="left:640px;top:168px;width:360px;border-top:2px dotted rgba(255,255,255,.8)"></div>
  <svg class="abs" style="left:565px;top:133px" width="70" height="70" viewBox="0 0 70 70"><circle cx="35" cy="35" r="33" fill="#fff"/><path d="M22 42c0-9 4-14 10-16v5c-3 1-4 3-4 6h4v9h-10zM38 42c0-9 4-14 10-16v5c-3 1-4 3-4 6h4v9h-10z" fill="#1a6fc4"/></svg>
  <svg class="abs" style="left:102px;top:233px" width="30" height="30"><circle cx="15" cy="15" r="13" fill="none" stroke="#fff" stroke-width="2"/><path d="M17 9l-6 6 6 6" stroke="#fff" stroke-width="2" fill="none"/></svg>
  <svg class="abs" style="left:1068px;top:233px" width="30" height="30"><circle cx="15" cy="15" r="13" fill="none" stroke="#fff" stroke-width="2"/><path d="M13 9l6 6-6 6" stroke="#fff" stroke-width="2" fill="none"/></svg>
  <p class="abs quote">I was able to get my 1st job only two weeks after finishing this program. It is the future of VFX training. Brightloom has changed my life and changed the way that I think about the world around me. I would highly recommend this program above any other, to anyone wishing to pursue a career in the film industry.</p>
  <div class="abs" style="left:486px;top:320px;width:86px;height:86px;border-radius:50%;border:3px solid #fff;background:linear-gradient(160deg,#c8b4a2,#7a6658)" role="img" aria-label="Graduate portrait"></div>
  <p class="abs" style="left:587px;top:340px;color:#fff;font-family:'Jost',Arial,sans-serif;font-size:17px">-Dana Whitfield</p>
  <p class="abs" style="left:587px;top:366px;color:#fff;font-size:12px;font-style:italic;font-weight:600">Lighting Artist Graduate</p>
</section>

<section class="section" style="top:2977px;height:446px">
  <h2 class="abs heading" style="left:133px;top:60px;font-size:26px">The Brightloom Advantage</h2>
  <div class="rule" style="left:133px;top:106px"></div>
  <p class="abs lead" style="left:133px;top:122px">A program designed by industry, for industry</p>
  <p class="abs copy" style="left:133px;top:156px;width:600px">There's a reason why each of our graduates have found work in their field. We don't sell courses, we provide relevant training. In order to bring out the best in our students, we run a program that we know will maximize each student's potential.</p>
  <p class="abs" style="left:133px;top:226px;width:630px;color:var(--blue);font-size:11.5px;line-height:17px;font-weight:600">Brightloom offers an un-paralleled training experience. Here are a few examples of what makes our school unique:</p>
  <ol class="abs numbered" style="left:133px;top:258px">
    <li><span class="num">1</span>Affordable tuition for both domestic and international students</li>
    <li><span class="num">2</span>A faculty of 12 world-class industry masters</li>
    <li><span class="num">3</span>Maximum class size of 12 students</li>
    <li><span class="num">4</span>One-on-one mentorship</li>
  </ol>
  <ol class="abs numbered" style="left:540px;top:258px">
    <li><span class="num">5</span>Employment opportunities</li>
    <li><span class="num">6</span>Employment opportunities</li>
    <li><span class="num">7</span>And more!</li>
  </ol>
  <div class="photo-ring" style="left:789px;top:85px"><div class="photo" role="img" aria-label="Graduates holding their certificates" style="background:radial-gradient(circle at 50% 45%,#b9a496,#5a4a48 50%,#17181c 85%)"></div></div>
</section>

<section class="section cta">
  <p style="position:absolute;top:22px;width:1200px;font-size:21px">Want to learn more?</p>
  <p style="position:absolute;top:56px;width:1200px;font-size:27px;text-transform:uppercase;letter-spacing:.5px">Fill out the form above to receive information about the program!</p>
</section>

<footer class="section site-footer">
  <div class="abs footer-brand">
    <div class="footer-dot"></div>
    <span class="footer-name">BRIGHTLOOM</span>
  </div>
  <p class="abs copyright">Copyright © 2017 Brightloom Academy of 3D Animation &amp; VFX.<br>All Rights Reserved.</p>
  <div class="abs" style="left:893px;top:28px;display:flex;align-items:center;gap:6px;font-size:11px;color:var(--body)">
    <span style="margin-right:6px">Follow Us :</span>
    <span class="social"></span><span class="social"></span><span class="social"></span><span class="social"></span>
  </div>
</footer>

</body>
</html>
```